Meadowlark Property Review is a leading provider of residential appraisal and home inspection products in S

I need a business card/logo designed that obviously describes my business. We are a residential appraisal and home inspection company in Springfield, MO. We offer residential appraisals, home inspection, pest inspection and radon gas measurement. We have been in business for 18 years and hold state certified residential appraisal licenses and OBREX certified home inspection licenses. I have a logo that I really like and will attach, but would be open to new suggestions. I like more modern designs than traditional and would like a two sided card with our services, licenses and qualifications on the back.

```html
<!DOCTYPE html>
<html lang="en">
<head>
<meta charset="utf-8">
<title>Meadowlark Property Review – Business Card</title>
<link rel="stylesheet" href="https://fonts.googleapis.com/css2?family=Source+Sans+3:ital,wght@0,400;0,600;0,700;1,400&display=swap">
<style>
  :root {
    --page-bg: #d9d3cc;
    --card-light: #ece8e3;
    --card-light-edge: #dcd6cf;
    --brown: #6b4a32;
    --brown-dark: #553823;
    --brown-text: #5a4131;
    --orange: #e2751f;
    --cream: #f3ece4;
    --services: #f0b184;
  }
  * { margin: 0; padding: 0; box-sizing: border-box; }
  html, body {
    width: 1200px;
    height: 969px;
    overflow: hidden;
    background: var(--page-bg);
    font-family: "Source Sans 3", "Myriad Pro", Arial, sans-serif;
  }
  .card {
    position: absolute;
    left: 100px;
    top: 202px;
    width: 1000px;
    height: 564px;
    border-radius: 36px;
    overflow: hidden;
    background: linear-gradient(160deg, var(--card-light) 0%, var(--card-light-edge) 100%);
    box-shadow: 0 18px 40px rgba(60, 40, 25, 0.25);
  }
  .card-swoosh {
    position: absolute;
    inset: 0;
    width: 1000px;
    height: 564px;
  }
  .brand {
    position: absolute;
    left: 82px;
    top: 70px;
    display: flex;
    align-items: flex-start;
    gap: 18px;
  }
  .brand-mark {
    width: 22px;
    height: 22px;
    margin-top: 14px;
    background: var(--orange);
  }
  .brand-name {
    font-weight: 700;
    font-size: 50px;
    line-height: 1.0;
    color: var(--brown-text);
    letter-spacing: -0.5px;
  }
  .person {
    position: absolute;
    left: 82px;
    top: 262px;
  }
  .person-name {
    font-weight: 600;
    font-size: 32px;
    color: var(--brown-text);
    line-height: 1.2;
  }
  .person-title {
    font-size: 24px;
    color: var(--orange);
    line-height: 1.3;
  }
  .contact {
    position: absolute;
    right: 70px;
    top: 232px;
    text-align: right;
    color: var(--cream);
  }
  .address {
    font-size: 23px;
    line-height: 1.25;
    margin-bottom: 14px;
  }
  .contact-line {
    display: flex;
    justify-content: flex-end;
    align-items: center;
    gap: 14px;
    font-size: 23px;
    height: 39px;
  }
  .contact-icon {
    width: 24px;
    height: 24px;
    flex: none;
  }
  .services {
    margin-top: 16px;
    font-style: italic;
    font-size: 24px;
    line-height: 1.35;
    color: var(--services);
  }
</style>
</head>
<body>
  <div class="card">
    <svg class="card-swoosh" viewBox="0 0 1000 564" aria-hidden="true">
      <defs>
        <linearGradient id="brownFill" x1="0" y1="1" x2="1" y2="0">
          <stop offset="0" stop-color="#5a3b25"/>
          <stop offset="1" stop-color="#7a5840"/>
        </linearGradient>
      </defs>
      <path d="M20 564 C250 430 420 210 700 178 C820 164 930 158 1000 158 L1000 564 Z" fill="url(#brownFill)"/>
      <path d="M28 548 C255 405 430 192 700 158 C820 143 925 136 1000 140 L1000 146 C925 144 822 152 702 168 C436 204 262 418 34 556 Z" fill="var(--orange)"/>
    </svg>

    <div class="brand">
      <div class="brand-mark"></div>
      <div class="brand-name">Meadowlark<br>Property Review</div>
    </div>

    <div class="person">
      <div class="person-name">Evan Hartley</div>
      <div class="person-title">CEO/Founder</div>
    </div>

    <div class="contact">
      <div class="address">214 Walnut Ridge Road<br>Springfield, Missouri 65804</div>

      <div class="contact-line">
        <span>417 555 0148</span>
        <svg class="contact-icon" viewBox="0 0 24 24" aria-hidden="true">
          <path d="M6 3 L9 3 L10.5 8 L8.5 9.5 C9.5 12 12 14.5 14.5 15.5 L16 13.5 L21 15 L21 18 C21 19.5 20 21 18 21 C10 20.5 3.5 14 3 6 C3 4 4.5 3 6 3 Z" fill="var(--cream)"/>
        </svg>
      </div>
      <div class="contact-line">
        <span>417 555 0193</span>
        <svg class="contact-icon" viewBox="0 0 24 24" aria-hidden="true">
          <rect x="6" y="3" width="12" height="6" fill="var(--cream)"/>
          <rect x="2" y="10" width="20" height="8" rx="1.5" fill="var(--cream)"/>
          <rect x="6" y="15" width="12" height="6" fill="var(--cream)" stroke="#6b4a32" stroke-width="1"/>
        </svg>
      </div>
      <div class="contact-line">
        <span>evan@mpreview.com</span>
        <svg class="contact-icon" viewBox="0 0 24 24" aria-hidden="true">
          <rect x="2" y="5" width="20" height="14" fill="var(--cream)"/>
          <path d="M2.5 5.5 L12 13 L21.5 5.5" fill="none" stroke="#6b4a32" stroke-width="1.5"/>
        </svg>
      </div>
      <div class="contact-line">
        <span>www.mpreview.com</span>
        <svg class="contact-icon" viewBox="0 0 24 24" aria-hidden="true">
          <circle cx="12" cy="12" r="10" fill="var(--cream)"/>
          <ellipse cx="12" cy="12" rx="4.5" ry="10" fill="none" stroke="#6b4a32" stroke-width="1.3"/>
          <path d="M2 12 H22 M4 7 H20 M4 17 H20" stroke="#6b4a32" stroke-width="1.3"/>
        </svg>
      </div>

      <div class="services">Residential appraisals | Home inspection<br>Pest inspection and radon gas measurement.</div>
    </div>
  </div>
</body>
</html>
```